Pre-workout label and Super Greens label for Brightmoor Nutrition Supplements

I need a label design for Club Brightmoor's 2 supplements. The first is a Pre-workout. The Pre-workout label needs to be 11.25 x 2.5 inches. This label will go on a black container. The second is a Super-Green. The Super-Green label should be 11.25 x 4.25 inches and will go on a white container. We have been selling these for a few years but the current labels are a little meh. I'd like something trendier and bolder. Must keep the Club Brightmoor branding. All the nurtition data must appear . I attached the current designs so you can know the flavors, nutrtional data etc. Thank you!
Updates

I can upload the Club Brightmoor logo! If anyone can tell me how to do that.

```html
<!DOCTYPE html>
<html lang="en">
<head>
<meta charset="utf-8">
<title>Super Greens Label – Brightmoor Nutrition</title>
<link rel="stylesheet" href="https://fonts.googleapis.com/css2?family=Alfa+Slab+One&family=Montserrat:wght@500;600;700;800&display=swap">
<style>
  :root {
    --page: #ffffff;
    --leaf-dark: #0f2412;
    --leaf-mid: #2a5a24;
    --leaf-light: #3f7a30;
    --lime: #8cc63f;
    --forest: #1d5a3a;
    --white: #ffffff;
    --ink: #111111;
    --muted-ink: #2b3b22;
  }
  * { box-sizing: border-box; margin: 0; padding: 0; }
  html, body { width: 800px; height: 1200px; overflow: hidden; background: var(--page); }
  body { position: relative; font-family: "Montserrat", sans-serif; }

  .label {
    position: absolute; left: 20px; top: 448px;
    width: 760px; height: 304px;
    border-radius: 20px; overflow: hidden;
    color: var(--white);
  }
  .label__foliage {
    position: absolute; inset: 0;
    background:
      radial-gradient(ellipse at 30% 35%, var(--leaf-light) 0%, transparent 45%),
      radial-gradient(ellipse at 75% 65%, var(--leaf-mid) 0%, transparent 50%),
      radial-gradient(ellipse at 10% 85%, var(--leaf-mid) 0%, transparent 40%),
      linear-gradient(135deg, var(--leaf-dark), var(--leaf-mid) 50%, var(--leaf-dark));
  }

  /* Left panel */
  .directions-panel {
    position: absolute; left: 43px; top: 50px; width: 83px; height: 193px;
    background: var(--white); color: var(--forest);
    text-align: center; padding: 8px 4px;
  }
  .directions-panel__title {
    font-family: "Alfa Slab One", serif; font-size: 11px; line-height: 10px;
    color: var(--forest); margin-bottom: 10px;
  }
  .directions-panel p { font-size: 5.2px; line-height: 6.4px; font-weight: 500; margin-bottom: 7px; }
  .fda-note {
    position: absolute; left: 43px; top: 262px; width: 83px; height: 20px;
    background: var(--white); color: var(--ink);
    font-size: 2.6px; line-height: 3.1px; text-align: center; padding: 3px 4px;
  }

  /* Front panel */
  .front { position: absolute; left: 200px; top: 0; width: 292px; height: 304px; text-align: center; }
  .brand {
    position: absolute; top: 47px; left: 0; width: 100%;
    font-size: 8.5px; font-weight: 700; letter-spacing: 1.2px; text-transform: uppercase;
  }
  .brand__mark {
    display: block; width: 12px; height: 12px; margin: 0 auto 6px;
    background: var(--white);
  }
  .brand { top: 30px; }
  .product-name {
    position: absolute; top: 78px; left: 0; width: 100%;
    font-family: "Alfa Slab One", serif; font-size: 31px; line-height: 33px;
    letter-spacing: 1px; color: var(--white);
  }
  .flavor {
    position: absolute; top: 166px; left: 102px; width: 89px; height: 12px;
    background: var(--white); color: var(--lime); border-radius: 3px;
    font-size: 7px; font-weight: 700; letter-spacing: 0.8px; line-height: 12px;
  }
  .benefits { position: absolute; top: 210px; left: 40px; width: 212px; display: flex; justify-content: space-between; }
  .benefit { width: 66px; display: flex; flex-direction: column; align-items: center; }
  .benefit svg { width: 26px; height: 26px; margin-bottom: 3px; }
  .benefit span { font-size: 7.6px; font-weight: 700; line-height: 7.8px; text-transform: uppercase; letter-spacing: 0.3px; }
  .front__meta {
    position: absolute; top: 279px; font-size: 4.8px; font-weight: 700; letter-spacing: 0.2px;
  }
  .front__meta--left { left: 58px; }
  .front__meta--right { left: 198px; }

  /* Supplement facts */
  .facts {
    position: absolute; left: 553px; top: 20px; width: 185px; height: 244px;
    background: var(--white); color: var(--ink);
    border: 1.5px solid var(--forest); padding: 2px 2px;
    font-size: 3.7px; line-height: 4.6px; font-weight: 600;
  }
  .facts__title { font-family: "Montserrat", sans-serif; font-weight: 800; font-size: 9px; line-height: 10px; }
  .facts__serving { font-weight: 700; border-bottom: 2px solid var(--ink); padding-bottom: 1px; }
  .facts__row {
    display: grid; grid-template-columns: 1fr 30px 14px;
    border-bottom: 0.5px solid var(--ink); padding: 0.7px 0;
  }
  .facts__row--head { font-weight: 700; border-bottom: 1px solid var(--ink); }
  .facts__row--head span:first-child { text-align: right; padding-right: 4px; }
  .facts__row--indent span:first-child { padding-left: 4px; }
  .facts__row--blend { align-items: center; border-bottom: 1px solid var(--ink); padding: 1.2px 0; }
  .facts__row--blend span { font-size: 3.2px; line-height: 3.9px; }
  .facts__row--blend b { display: block; font-weight: 700; }
  .facts__foot { font-size: 3.2px; line-height: 3.9px; padding-top: 1px; }

  .other-ingredients {
    position: absolute; left: 553px; top: 267px; width: 185px;
    font-size: 3.6px; line-height: 4.3px; color: var(--muted-ink);
  }
  .formulated { position: absolute; left: 553px; top: 283px; font-size: 4.4px; color: var(--white); }
  .formulated b { font-weight: 700; }
</style>
</head>
<body>
<section class="label">
  <div class="label__foliage" role="img" aria-label="Full-bleed photograph of dark green tropical leaves"></div>

  <aside class="directions-panel">
    <h2 class="directions-panel__title">SUPER<br>GREENS</h2>
    <p>Directions: Mix one (1) scoop into 6-8oz of your favorite non-citrus juice, water, smoothie, or protein shake.</p>
    <p>CAUTION: As with any dietary supplement, consult your healthcare practitioner before using this product, especially if you are pregnant, nursing, anticipate surgery, take medication on a regular basis or are otherwise under medical supervision. Store in a cool, dry place. Keep out of reach of children.</p>
  </aside>
  <p class="fda-note">*These statements have not been evaluated by the Food and Drug Administration. This product is not intended to diagnose, treat, cure or prevent any disease.</p>

  <main class="front">
    <div class="brand"><span class="brand__mark"></span>Brightmoor Nutrition</div>
    <h1 class="product-name">SUPER<br>GREENS</h1>
    <div class="flavor">APPLE CINNAMON</div>
    <ul class="benefits">
      <li class="benefit">
        <svg viewBox="0 0 26 26" fill="none" stroke="#8cc63f" stroke-width="1.4">
          <circle cx="9" cy="5" r="1.6"/><circle cx="15" cy="4" r="1.2"/><circle cx="13" cy="9" r="1.8"/><circle cx="18" cy="11" r="1.4"/><circle cx="7" cy="11" r="1.2"/>
          <path d="M4 20 q6 -5 12 -2 l5 -2 q2 1 0 3 l-8 4 h-9 z"/>
        </svg>
        <span>Detox<br>Body*</span>
      </li>
      <li class="benefit">
        <svg viewBox="0 0 26 26" fill="none" stroke="#8cc63f" stroke-width="1.4">
          <circle cx="13" cy="13" r="7"/><circle cx="13" cy="13" r="3"/>
          <path d="M13 2v3M13 21v3M2 13h3M21 13h3M5 5l2 2M19 19l2 2M5 21l2-2M19 7l2-2"/>
        </svg>
        <span>Promote<br>Healthy<br>Digestion*</span>
      </li>
      <li class="benefit">
        <svg viewBox="0 0 26 26" fill="none" stroke="#8cc63f" stroke-width="1.4">
          <path d="M13 22 L4 13 A5 5 0 0 1 13 6 A5 5 0 0 1 22 13 Z"/>
          <path d="M16 14 l4 -1.5 l4 1.5 v3 q0 3 -4 5 q-4 -2 -4 -5 z"/>
        </svg>
        <span>Support<br>Immunity*</span>
      </li>
    </ul>
    <div class="front__meta front__meta--left">DIETARY SUPPLEMENT</div>
    <div class="front__meta front__meta--right">30 SERVINGS &nbsp;&nbsp;270G (9.5OZ)</div>
  </main>

  <section class="facts">
    <h2 class="facts__title">Supplement Facts</h2>
    <div class="facts__serving">Serving Size: Approx. 1 Scoop (9 g)<br>Servings per Container: 30</div>
    <div class="facts__row facts__row--head"><span>Amount per Serving</span><span></span><span>%DV</span></div>
    <div class="facts__row"><span>Calories</span><span>40</span><span></span></div>
    <div class="facts__row"><span>Total Fat</span><span>1.5 g</span><span>2%</span></div>
    <div class="facts__row"><span>Total Carbohydrates</span><span>5 g</span><span>2%</span></div>
    <div class="facts__row facts__row--indent"><span>Dietary Fiber</span><span>2 g</span><span>7%</span></div>
    <div class="facts__row facts__row--indent"><span>Total Sugars</span><span>&lt;1 g</span><span></span></div>
    <div class="facts__row"><span>Protein</span><span>2 g</span><span></span></div>
    <div class="facts__row"><span>Vitamin E (as Dl-Alpha Tocopheryl Acetate)</span><span>46 mg</span><span>307%</span></div>
    <div class="facts__row"><span>Calcium</span><span>30 mg</span><span>2%</span></div>
    <div class="facts__row"><span>Iron</span><span>2.5 mg</span><span>14%</span></div>
    <div class="facts__row"><span>Sodium</span><span>15 mg</span><span>1%</span></div>
    <div class="facts__row"><span>Potassium</span><span>110 mg</span><span>2%</span></div>
    <div class="facts__row facts__row--blend"><span><b>Green Health Blend</b>Soy Lecithin Powder, Apple Fruit Powder, Barley Grass Powder, Alfalfa Herb Powder, Wheat Grass Powder, Wheat Sprout Powder, Barley Seed Malt Powder, Rice Bran Powder, Dulse Powder, Spinach Leaf Powder</span><span>5.8 g</span><span>†</span></div>
    <div class="facts__row facts__row--blend"><span><b>Energy Blend*</b>Spirulina Whole Plant Powder, Beet Root Powder, Bee Pollen Powder, Green Tea Leaf Extract</span><span>1.41 g</span><span>†</span></div>
    <div class="facts__row facts__row--blend"><span><b>Detox Blend*</b>Acerola Berry Powder, Parsley Leaf Powder, Deglycyrrhizinated (DGL) Licorice Root Powder, Echinacea angustifolia Herb Powder, Astragalus Root Powder, Milk Thistle Seed Extract</span><span>420 mg</span><span>†</span></div>
    <div class="facts__row facts__row--blend"><span><b>Alkalinity Blend*</b>Chlorella Cracked Cell Wall Powder, Suma Root Powder, Ginkgo Leaf Extract, Grape Seed Extract</span><span>340 mg</span><span>†</span></div>
    <div class="facts__row facts__row--blend"><span><b>Probiotic Blend Complex</b>Inulin, Lactobacillus acidophilus, Lactobacillus bulgaricus, Bifidobacterium bifidum, Bifidobacterium longum, Streptococcus thermophilus</span><span>150 mg</span><span>†</span></div>
    <div class="facts__row facts__row--blend"><span><b>Enzyme Blend</b>Maltodextrin, Inulin, Bromelain, Papain, Cellulase, Lipase, Protease</span><span>125 mg</span><span>†</span></div>
    <p class="facts__foot">Percent Daily Values are based on a 2,000 calorie diet<br>† Daily Value (DV) not established</p>
  </section>

  <p class="other-ingredients">Other Ingredients: Organic Cassia Bark Powder, Natural Flavor, Silicon Dioxide, Rebaudioside A (from Stevia Leaf Extract), Sucralose. Contains: Soy, Tree Nuts, Wheat, and Milk.</p>
  <p class="formulated"><b>Formulated by:</b> Club Brightmoor, 480 Fernhill Rd, Alder, WY 82000 (555) 014-2290</p>
</section>
</body>
</html>
```